Summit Ridge Business Card

Side 1: Summit Ridge Logo (logo without Maltese cross) with industrial rope rescue related theme. Our company services - TRAINING - Fire Training, Confined Space Rescue Training, Rope Rescue training, Hazmat Training, Incident Command, EMS, Pump Operations Training. Website - summitridgeexample.com.
Side 2: Summit Ridge Fire Department Logo (logo with Maltese cross) with Firefighter related theme. Company (division) services - FIELD SERVICES - Fire Department, Stand-by Rescue, Safety, EMS, Planning. "Supporting the Emergency Response Community Since 1967"

Add contact information wherever it makes since (Name, Email, Phone).
I would like it to represent the Summit Ridge Fire Department Logo as a division not as a separate entity without saying it, possibly by depicting it in the background of Side 2 instead of being a standalone picture like the logo on Side 1.

```html
<!DOCTYPE html>
<html lang="en">
<head>
<meta charset="utf-8">
<title>Summit Ridge Business Card</title>
<link href="https://fonts.googleapis.com/css2?family=Poppins:wght@400;500;600;700;800&display=swap" rel="stylesheet">
<style>
  :root{
    --bg:#e4e1dc;
    --card-dark:#1c1c1d;
    --card-light:#ffffff;
    --red:#f20d0d;
    --red-text:#ee2a1b;
    --ink:#111111;
    --white:#ffffff;
    --faint:#fbe5e5;
  }
  *{box-sizing:border-box;margin:0;padding:0}
  html,body{width:1200px;height:900px;overflow:hidden}
  body{background:var(--bg);font-family:"Poppins",sans-serif;position:relative}
  .card{position:absolute;width:700px;height:400px;overflow:hidden;box-shadow:0 12px 30px rgba(0,0,0,.25)}

  /* Side 1 */
  .card--training{left:40px;top:40px;background:var(--card-dark);color:var(--white)}
  .brand{position:absolute;right:48px;top:52px;display:flex;align-items:center;gap:14px}
  .brand__dot{width:22px;height:22px;border-radius:50%;background:var(--red)}
  .brand__name{font-weight:800;font-size:38px;letter-spacing:1px;color:var(--red);text-transform:uppercase}
  .services{position:absolute;left:48px;top:152px}
  .services__title{font-weight:700;font-size:26px;line-height:34px;letter-spacing:1px;color:var(--red);text-transform:uppercase;margin-bottom:4px}
  .services__list{list-style:none}
  .services__list li{display:flex;align-items:center;gap:12px;font-size:18px;line-height:26px;font-weight:500}
  .services__list li::before{content:"";width:10px;height:10px;border-radius:50%;background:var(--red);flex:none}
  .website{position:absolute;right:48px;top:250px;font-size:17px;font-weight:500}
  .website span{color:var(--red)}

  /* Side 2 */
  .card--field{left:460px;top:460px;background:var(--card-light);color:var(--ink)}
  .backdrop-mark{position:absolute;right:40px;top:-30px;width:300px;height:300px;border-radius:50%;border:26px solid var(--faint)}
  .wave{position:absolute;inset:0;width:700px;height:400px}
  .field{position:absolute;left:56px;top:28px}
  .field .services__title{font-size:24px;line-height:32px;color:var(--red-text);margin-bottom:2px}
  .field__list{list-style:none}
  .field__list li{display:flex;align-items:center;gap:10px;font-size:18px;line-height:24px;font-weight:500}
  .field__list li::before{content:"";width:8px;height:8px;border-radius:50%;background:var(--red-text);flex:none}
  .contact{position:absolute;left:76px;top:184px}
  .contact__name{font-weight:700;font-size:28px;line-height:34px}
  .contact__row{display:flex;align-items:center;gap:10px;font-size:18px;line-height:28px;font-weight:500}
  .contact__row svg{width:18px;height:18px;flex:none}
  .tagline{position:absolute;right:40px;bottom:28px;text-align:right;color:var(--red-text);font-weight:600;font-size:17px;line-height:22px}
</style>
</head>
<body>

<section class="card card--training" aria-label="Side 1">
  <div class="brand">
    <span class="brand__dot"></span>
    <span class="brand__name">Summit Ridge</span>
  </div>
  <div class="services">
    <h2 class="services__title">Training</h2>
    <ul class="services__list">
      <li>Fire Training</li>
      <li>Confined Space Rescue Training</li>
      <li>Rope Rescue training</li>
      <li>Hazmat Training</li>
      <li>Incident Command</li>
      <li>EMS</li>
      <li>Pump Operations Training</li>
    </ul>
  </div>
  <p class="website">www.<span>summitridgeexample</span>.com</p>
</section>

<section class="card card--field" aria-label="Side 2">
  <div class="backdrop-mark" aria-hidden="true"></div>
  <svg class="wave" viewBox="0 0 700 400" aria-hidden="true">
    <path d="M0 330 C240 355 440 300 560 225 C470 298 260 372 0 372 Z" fill="var(--red)"/>
    <path d="M0 362 C260 378 500 290 700 180 L700 400 L0 400 Z" fill="var(--card-dark)"/>
  </svg>
  <div class="field">
    <h2 class="services__title">Field Services</h2>
    <ul class="field__list">
      <li>Fire Department</li>
      <li>Stand-by Rescue</li>
      <li>Safety</li>
      <li>EMS</li>
      <li>Planning</li>
    </ul>
  </div>
  <div class="contact">
    <p class="contact__name">Daniel Carter</p>
    <p class="contact__row">
      <svg viewBox="0 0 24 24"><path d="M6.6 10.8a15 15 0 0 0 6.6 6.6l2.2-2.2a1 1 0 0 1 1-.25 11.4 11.4 0 0 0 3.6.57 1 1 0 0 1 1 1V20a1 1 0 0 1-1 1A17 17 0 0 1 3 4a1 1 0 0 1 1-1h3.5a1 1 0 0 1 1 1c0 1.25.2 2.45.57 3.57a1 1 0 0 1-.25 1z" fill="var(--red-text)"/></svg>
      044-555 010 200
    </p>
    <p class="contact__row">
      <svg viewBox="0 0 24 24"><rect x="2" y="5" width="20" height="14" fill="var(--red-text)"/><path d="M2 5l10 8 10-8" fill="none" stroke="#fff" stroke-width="1.6"/></svg>
      info@summitridgeexample.com
    </p>
  </div>
  <p class="tagline">Supporting the Emergency Response<br>Community Since 1967</p>
</section>

</body>
</html>
```